Youth Lifting Youth Business Card. We have existing logo

We need a business card design from an existing logo.
Our logo is in black and white but would love to add in the color burgundy but we're open to any color. Our website is www.youthliftingyouthmv.org

Target Market(s)

corporations and foundations who will be donating

Industry/Entity Type

Business

Contact Information for Business Card

Address: 2318 Marwick Ave Alder Springs, OR 97999
Name: Corin Halvorsen
Founder email: corin.halvorsen@youthliftingyouthmv.org
Phone: 555-637-9081

Requirements
Nice to have
• Our colors are burgundy and white, but that's not a necessity

```html
<!DOCTYPE html>
<html lang="en">
<head>
<meta charset="utf-8">
<title>Youth Lifting Youth — Business Card</title>
<link rel="stylesheet" href="https://fonts.googleapis.com/css2?family=Tinos:wght@400;700&display=swap">
<style>
  :root {
    --page: #e4e4e2;
    --card: #ffffff;
    --ink: #111111;
    --black: #0a0a0a;
    --band-light: #e2e2e2;
    --band-dark: #9a9a9a;
    --muted: #333333;
  }
  * { margin: 0; padding: 0; box-sizing: border-box; }
  html, body { width: 1200px; height: 817px; overflow: hidden; }
  body { background: var(--page); font-family: "Tinos", "Times New Roman", serif; color: var(--ink); }

  .card {
    position: absolute; left: 160px; top: 158px;
    width: 880px; height: 500px;
    background: var(--card);
    overflow: hidden;
    box-shadow: 0 12px 30px rgba(0,0,0,.25);
  }
  .card-shapes { position: absolute; inset: 0; }

  .brand {
    position: absolute; left: 20px; top: 190px; width: 180px;
    display: flex; flex-direction: column; align-items: center; gap: 14px;
  }
  .brand-dot { width: 64px; height: 64px; border-radius: 50%; background: var(--card); }
  .brand-name { color: var(--card); font-size: 20px; font-weight: 400; text-align: center; line-height: 1.2; }

  .identity { position: absolute; right: 110px; top: 38px; text-align: right; }
  .person-name { font-size: 58px; font-weight: 700; letter-spacing: .5px; line-height: 1; }
  .person-role { font-size: 18px; margin-top: 6px; color: var(--muted); }

  .contact { position: absolute; right: 110px; top: 232px; list-style: none; text-align: right; }
  .contact li { font-size: 20px; line-height: 34px; display: flex; justify-content: flex-end; align-items: center; gap: 14px; }
  .contact svg { width: 18px; height: 18px; fill: var(--black); flex: none; }

  .tab { position: absolute; right: 0; background: var(--black); }
  .tab-top { top: 22px; width: 70px; height: 74px; }
  .tab-contact { top: 226px; width: 70px; height: 110px; }
</style>
</head>
<body>
  <section class="card" aria-label="Business card front">
    <svg class="card-shapes" width="880" height="500" viewBox="0 0 880 500" aria-hidden="true">
      <defs>
        <linearGradient id="band" x1="0" y1="0" x2="1" y2="0">
          <stop offset="0" stop-color="#9a9a9a"/>
          <stop offset="1" stop-color="#e2e2e2"/>
        </linearGradient>
      </defs>
      <path d="M0 0 H340 Q150 250 340 500 H0 Z" fill="url(#band)"/>
      <path d="M0 0 H305 Q120 250 305 500 H0 Z" fill="#0a0a0a"/>
    </svg>

    <div class="brand">
      <span class="brand-dot"></span>
      <span class="brand-name">Youth Lifting Youth</span>
    </div>

    <div class="identity">
      <h1 class="person-name">Corin Halvorsen</h1>
      <p class="person-role">Founder</p>
    </div>

    <ul class="contact">
      <li><span>555-637-9081</span>
        <svg viewBox="0 0 24 24"><path d="M6.6 10.8a15 15 0 0 0 6.6 6.6l2.2-2.2c.3-.3.7-.4 1-.2 1.1.4 2.3.6 3.6.6.6 0 1 .4 1 1V20c0 .6-.4 1-1 1A17 17 0 0 1 3 4c0-.6.4-1 1-1h3.5c.6 0 1 .4 1 1 0 1.3.2 2.5.6 3.6.1.3 0 .7-.2 1z"/></svg></li>
      <li><span>corin.halvorsen@youthliftingyouthmv.org</span>
        <svg viewBox="0 0 24 24"><path d="M2 5h20v14H2z M3.5 6.5 12 13l8.5-6.5" fill="none" stroke="#0a0a0a" stroke-width="2"/></svg></li>
      <li><span>2318 Marwick Ave Alder Springs, OR 97999</span>
        <svg viewBox="0 0 24 24"><path d="M12 2a7 7 0 0 0-7 7c0 5 7 13 7 13s7-8 7-13a7 7 0 0 0-7-7zm0 9.5A2.5 2.5 0 1 1 12 6.5a2.5 2.5 0 0 1 0 5z"/></svg></li>
    </ul>

    <div class="tab tab-top"></div>
    <div class="tab tab-contact"></div>
  </section>
</body>
</html>
```